GlassHaven Artbook for Okanagan Region, British Columbia

Creating an art book: GlassHaven, for the Okanagan Wine Region in British Columbia, Canada. Would like smart, modern, clean and linear...cool, sexy urban, not ugly boring suburban... I need a cover that appeals to the wino in all of us! Title: GlassHaven -Marla Dovicki
Updates
Thank you all kindly for your efforts. I have added some files so that you can get a sense of my aesthetic...it's never easy trying to figure it out, is it? I will hopefully have dimensions of book soon...cheers, Marla
would anyone please design a giant wine bottle with the wine label that looks like a label but says glasshaven...just curious to see if it works as a design or not...thank you.
Target Market(s)
Designing this wine art book of quotes to wineries in Okanagan BC. Buyer is wine lover and tourist ready to spend his vacation bucks on this wonderful book!
Look and feel

```html
<!DOCTYPE html>
<html lang="en">
<head>
<meta charset="UTF-8">
<title>GlassHaven — Book Cover and Spine</title>
<link rel="stylesheet" href="https://fonts.googleapis.com/css2?family=Jost:wght@300;400;500&display=swap">
<style>
  :root {
    --page: #ffffff;
    --board: #231f20;
    --hinge: #3b3738;
    --wine-red: #b01b21;
    --ink-white: #ffffff;
    --caption: #2b2b2b;
    --art-light: #d9d9d9;
    --art-mid: #a9a7a8;
  }

  * { margin: 0; padding: 0; box-sizing: border-box; }

  html, body {
    width: 1200px;
    height: 900px;
    overflow: hidden;
    background: var(--page);
    font-family: "Jost", "Helvetica Neue", Arial, sans-serif;
  }

  .canvas {
    position: relative;
    width: 1200px;
    height: 900px;
  }

  /* Spine */
  .spine {
    position: absolute;
    left: 200px;
    top: 36px;
    width: 76px;
    height: 784px;
    background: var(--board);
  }

  .spine-dot {
    position: absolute;
    left: 18px;
    top: 32px;
    width: 40px;
    height: 40px;
    border-radius: 50%;
    background: var(--wine-red);
  }

  .spine-title {
    position: absolute;
    left: 0;
    top: 96px;
    width: 76px;
    writing-mode: vertical-rl;
    font-weight: 300;
    font-size: 40px;
    line-height: 76px;
    color: var(--ink-white);
    letter-spacing: 0.01em;
    white-space: nowrap;
  }

  .spine-subtitle {
    position: absolute;
    left: 0;
    top: 556px;
    width: 76px;
    writing-mode: vertical-rl;
    font-weight: 500;
    font-size: 12px;
    line-height: 76px;
    letter-spacing: 0.22em;
    color: var(--ink-white);
    white-space: nowrap;
  }

  /* Front cover */
  .front-cover {
    position: absolute;
    left: 468px;
    top: 36px;
    width: 532px;
    height: 784px;
    background: var(--board);
  }

  .hinge-line {
    position: absolute;
    left: 22px;
    top: 0;
    width: 5px;
    height: 100%;
    background: var(--hinge);
  }

  .cover-art {
    position: absolute;
    left: 190px;
    top: 118px;
    width: 212px;
    height: 380px;
    border-radius: 6px;
    background: linear-gradient(180deg, var(--art-light), var(--art-mid));
    opacity: 0.55;
  }

  .cover-title {
    position: absolute;
    left: 60px;
    right: 0;
    top: 598px;
    text-align: center;
    font-weight: 300;
    font-size: 88px;
    line-height: 1;
    color: var(--wine-red);
    letter-spacing: 0.005em;
    white-space: nowrap;
  }

  .cover-subtitle {
    position: absolute;
    left: 60px;
    right: 0;
    top: 696px;
    text-align: center;
    font-weight: 500;
    font-size: 22px;
    line-height: 1;
    letter-spacing: 0.12em;
    color: var(--ink-white);
    white-space: nowrap;
  }

  /* Captions */
  .caption {
    position: absolute;
    top: 849px;
    font-weight: 500;
    font-size: 12px;
    letter-spacing: 0.18em;
    color: var(--caption);
    white-space: nowrap;
  }

  .caption-spine { left: 200px; }
  .caption-front { left: 464px; }
</style>
</head>
<body>
  <main class="canvas">
    <section class="spine" aria-label="Spine of book">
      <span class="spine-dot"></span>
      <h2 class="spine-title">GlassHaven</h2>
      <p class="spine-subtitle">OKANAGAN WINE REGION</p>
    </section>

    <section class="front-cover" aria-label="Front cover of book">
      <span class="hinge-line"></span>
      <div class="cover-art" role="img" aria-label="Grape cluster illustration: rows of white circles with one red circle, topped by a green leaf"></div>
      <h1 class="cover-title">GlassHaven</h1>
      <p class="cover-subtitle">OKANAGAN WINE REGION</p>
    </section>

    <p class="caption caption-spine">SPINE OF BOOK</p>
    <p class="caption caption-front">FRONT COVER OF BOOK</p>
  </main>
</body>
</html>
```